Assessment Flyer

We are looking for a marketing flyer for our business. We are a psychology practice that has recently expanded our assessment team and availability. We need a flyer to fax to GP's and other referrers. We have previously sent out rather basic flyers as it was more of a courtesy update about our practice rather than a marketing tool. We have recently created a brochure just focusing on assessments which can be used as a guide for the flyer. We want to update them about our expansion, highlight the assessments we do, introduce our new psychologists, and touch on availability.

```html
<!DOCTYPE html>
<html lang="en">
<head>
<meta charset="utf-8">
<title>Assessment Services Flyer</title>
<link href="https://fonts.googleapis.com/css2?family=Poppins:wght@400;500;600;700;800&display=swap" rel="stylesheet">
<style>
  :root{
    --teal:#13a88f;
    --teal-dark:#0d7f6c;
    --green:#7dc242;
    --green-bright:#7ef03a;
    --green-dark:#5a9a2a;
    --ink:#1b1b1b;
    --page:#e6e6e6;
    --white:#ffffff;
  }
  *{margin:0;padding:0;box-sizing:border-box}
  html,body{width:1200px;height:2400px;overflow:hidden}
  body{background:var(--page);font-family:'Poppins',sans-serif;color:var(--ink);position:relative}
  .flyer{position:absolute;left:40px;top:408px;width:1120px;height:1584px;background:var(--white);overflow:hidden;box-shadow:0 18px 40px rgba(0,0,0,.25)}
  .header-art{position:absolute;left:0;top:0}
  .brand{position:absolute;left:60px;top:120px;display:flex;align-items:center;gap:12px;color:var(--white);font-weight:600;font-size:24px;line-height:1.1;width:420px}
  .brand-dot{width:30px;height:30px;border-radius:50%;background:var(--white);flex:none}
  .title{position:absolute;left:52px;top:240px;font-weight:800;line-height:1}
  .title .line1{display:block;color:var(--white);font-size:66px;letter-spacing:1px}
  .title .line2{display:block;color:var(--green-bright);font-size:100px;margin-top:-2px}
  .title-rule{position:absolute;left:53px;top:414px;width:50px;height:7px;background:var(--white)}
  .intro{position:absolute;left:53px;top:438px;width:480px;color:var(--white);font-size:19.5px;line-height:22.6px}
  .availability{position:absolute;left:53px;top:694px}
  .availability h2{color:var(--green);font-weight:700;font-size:33px;line-height:1;letter-spacing:.3px}
  .availability p{margin-top:10px;font-size:35px;font-weight:600;line-height:42px;display:flex;align-items:center;gap:14px}
  .availability .date{background:var(--teal);color:var(--white);font-weight:700;padding:0 24px;height:42px;display:inline-flex;align-items:center;font-size:33px}
  .team-heading{position:absolute;left:51px;top:836px;color:var(--green);font-weight:700;font-size:27px;line-height:1}
  .member{position:absolute;width:340px;height:96px}
  .member .tab{position:absolute;left:0;top:4px;width:26px;height:84px;clip-path:polygon(100% 0,100% 100%,0 100%,0 50%)}
  .member .name-bar{position:absolute;left:22px;top:4px;width:250px;height:44px;background:var(--white);box-shadow:0 -4px 8px rgba(0,0,0,.12);display:flex;align-items:center;padding-left:24px;font-weight:700;font-size:16.5px;line-height:16px;text-transform:none}
  .member .role-bar{position:absolute;left:10px;top:48px;width:258px;height:36px;clip-path:polygon(0 0,92% 0,100% 100%,0 100%);color:var(--white);font-size:13.5px;display:flex;align-items:center;padding-left:36px}
  .member .photo{position:absolute;left:250px;top:0;width:82px;height:82px;border-radius:50%;border:4px solid #dfe9d8;background:linear-gradient(160deg,#c9a48a,#6d4a3a)}
  .member.teal .tab{background:var(--teal-dark)}
  .member.teal .role-bar{background:var(--teal)}
  .member.green .tab{background:var(--green-dark)}
  .member.green .role-bar{background:var(--green)}
  .assessments-title{position:absolute;left:748px;top:722px;color:var(--teal);font-weight:700;font-size:25px;line-height:1;letter-spacing:.2px}
  .assessments-box{position:absolute;left:749px;top:758px;width:316px;height:680px;border:2px solid var(--green);border-top:none}
  .assessments-box::before,.assessments-box::after{content:"";position:absolute;top:0;height:2px;background:var(--green)}
  .assessment{position:absolute;left:0;width:316px;text-align:center;font-weight:600;font-size:22px;line-height:26px}
  .assessment .icon{display:block;margin:0 auto 8px;width:72px;height:72px;border-radius:50%;background:var(--teal);border:3px solid #bfe8de}
  .assessment.last span{background:var(--white);padding:0 10px}
  .contact{position:absolute;font-size:19px;line-height:22.5px;display:flex;gap:12px;align-items:flex-start}
  .contact svg{flex:none;margin-top:3px}
  .contact-divider{position:absolute;left:328px;top:1388px;width:1px;height:76px;background:#d3d3d3}
  .web-bar{position:absolute;left:649px;top:1480px;width:471px;height:38px;background:var(--teal);color:var(--white);font-weight:600;font-size:19px;display:flex;align-items:center;padding-left:20px}
</style>
</head>
<body>
<main class="flyer">
  <svg class="header-art" width="1120" height="680" viewBox="0 0 1120 680">
    <path d="M0,0 H520 Q640,30 720,90 L720,662 Q360,598 0,610 Z" fill="#7dc242"/>
    <path d="M0,22 Q380,20 700,110 L700,640 Q360,570 0,565 Z" fill="#13a88f"/>
    <circle cx="844" cy="353" r="302" fill="#7dc242"/>
    <circle cx="844" cy="353" r="278" fill="#13a88f"/>
    <circle cx="844" cy="353" r="272" fill="url(#photoTone)" role="img" aria-label="Photo of a smiling family reading a book together on a sofa"/>
    <defs>
      <linearGradient id="photoTone" x1="0" y1="0" x2="1" y2="1">
        <stop offset="0" stop-color="#f1ece4"/>
        <stop offset=".45" stop-color="#b9c3b8"/>
        <stop offset=".75" stop-color="#8a6a4e"/>
        <stop offset="1" stop-color="#d9a441"/>
      </linearGradient>
    </defs>
  </svg>

  <div class="brand"><span class="brand-dot"></span>Northgate Psychology &amp; Wellness</div>

  <h1 class="title"><span class="line1">ASSESSMENT</span><span class="line2">SERVICES</span></h1>
  <div class="title-rule"></div>
  <p class="intro">Northgate Psychology and Wellness is excited to announce the expansion of our assessment team. As the need for assessment services has grown, we have worked diligently to expand our team with highly skilled psychologists to support these needs.</p>

  <section class="availability">
    <h2>AVAILABILITY APPOINTMENTS</h2>
    <p>Available from Early <span class="date">MARCH 2024</span></p>
  </section>

  <h2 class="team-heading">MEET THE ASSESSMENT TEAM</h2>

  <div class="member teal" style="left:50px;top:880px"><div class="tab"></div><div class="role-bar">Clinical Director</div><div class="name-bar">Dr CLARA WHITFIELD</div><div class="photo" role="img" aria-label="Portrait of Dr Clara Whitfield"></div></div>
  <div class="member teal" style="left:400px;top:880px"><div class="tab"></div><div class="role-bar">Registered Psychologist</div><div class="name-bar">MARINA CASTELLANO</div><div class="photo" role="img" aria-label="Portrait of Marina Castellano"></div></div>

  <div class="member green" style="left:50px;top:996px"><div class="tab"></div><div class="role-bar">Registered Psychologist</div><div class="name-bar">Dr HELEN BARTON</div><div class="photo" role="img" aria-label="Portrait of Dr Helen Barton"></div></div>
  <div class="member green" style="left:400px;top:996px"><div class="tab"></div><div class="role-bar">Registered Psychologist</div><div class="name-bar">GABRIELA ORTIZ HALLOWAY</div><div class="photo" role="img" aria-label="Portrait of Gabriela Ortiz Halloway"></div></div>

  <div class="member teal" style="left:50px;top:1106px"><div class="tab"></div><div class="role-bar">Counselling Psychologist</div><div class="name-bar">Dr NADIA KESSLER</div><div class="photo" role="img" aria-label="Portrait of Dr Nadia Kessler"></div></div>
  <div class="member teal" style="left:400px;top:1106px"><div class="tab"></div><div class="role-bar">Provisional Psychologist</div><div class="name-bar">EMILY HARTWELL</div><div class="photo" role="img" aria-label="Portrait of Emily Hartwell"></div></div>

  <div class="member green" style="left:50px;top:1220px"><div class="tab"></div><div class="role-bar">Registered Psychologist</div><div class="name-bar">ROSA BELLAMONTE</div><div class="photo" role="img" aria-label="Portrait of Rosa Bellamonte"></div></div>
  <div class="member green" style="left:400px;top:1220px"><div class="tab"></div><div class="role-bar">Provisional Psychologist</div><div class="name-bar">JESSICA MOORE</div><div class="photo" role="img" aria-label="Portrait of Jessica Moore"></div></div>

  <h2 class="assessments-title">AVAILABLE ASSESSMENTS</h2>
  <div class="assessments-box">
    <div class="assessment" style="top:4px">
      <svg class="icon" viewBox="0 0 72 72"><g fill="none" stroke="#fff" stroke-width="2"><path d="M22 30 L36 23 L50 30 L36 37 Z"/><rect x="26" y="34" width="20" height="16"/><circle cx="36" cy="42" r="4"/></g></svg>
      Educational<br>Assessment
    </div>
    <div class="assessment" style="top:156px">
      <svg class="icon" viewBox="0 0 72 72"><g fill="none" stroke="#fff" stroke-width="2"><circle cx="30" cy="22" r="4"/><path d="M24 50 V32 H36 V50 M30 36 V50"/><circle cx="44" cy="32" r="3"/><path d="M40 50 V40 H48 V50"/></g></svg>
      ADHD: Children<br>&amp; Adults
    </div>
    <div class="assessment" style="top:300px">
      <svg class="icon" viewBox="0 0 72 72"><g fill="none" stroke="#fff" stroke-width="2"><path d="M26 24 H33 A3 3 0 0 1 39 24 H46 V31 A3 3 0 0 1 46 37 V46 H26 V37 A3 3 0 0 0 26 31 Z"/></g></svg>
      Autism: Children<br>&amp; Adults
    </div>
    <div class="assessment" style="top:446px">
      <svg class="icon" viewBox="0 0 72 72"><g fill="none" stroke="#fff" stroke-width="2"><circle cx="30" cy="20" r="4"/><path d="M30 26 V40 H42 L46 50"/><circle cx="34" cy="46" r="7"/></g></svg>
      Intellectual<br>Disability
    </div>
    <div class="assessment last" style="top:590px">
      <svg class="icon" viewBox="0 0 72 72"><g fill="none" stroke="#fff" stroke-width="2"><rect x="25" y="30" width="22" height="18"/><path d="M23 30 H49 M36 30 V48 M36 30 C30 20 26 26 36 30 C46 26 42 20 36 30"/></g></svg>
      <span>Giftedness</span>
    </div>
  </div>

  <div class="contact" style="left:53px;top:1388px">
    <svg width="14" height="18" viewBox="0 0 14 18"><path d="M7 0 A7 7 0 0 1 14 7 C14 12 7 18 7 18 C7 18 0 12 0 7 A7 7 0 0 1 7 0 Z" fill="#7dc242"/><circle cx="7" cy="7" r="2.5" fill="#fff"/></svg>
    <span>114 Harbour Road 3/27<br>Finch Terrace</span>
  </div>
  <div class="contact" style="left:53px;top:1452px">
    <svg width="16" height="16" viewBox="0 0 16 16"><path d="M3 1 L6 4 L4.5 6 C5.5 8.5 7.5 10.5 10 11.5 L12 10 L15 13 L13 15 C6 14 2 10 1 3 Z" fill="#13a88f"/></svg>
    <span>08 7000 1234</span>
  </div>
  <div class="contact" style="left:53px;top:1493px">
    <svg width="16" height="14" viewBox="0 0 16 14"><rect x="0" y="1" width="16" height="12" rx="1" fill="#7dc242"/><path d="M1 2 L8 8 L15 2" fill="none" stroke="#fff" stroke-width="1.5"/></svg>
    <span>hello@northgatewellness.com.au</span>
  </div>
  <div class="contact-divider"></div>
  <div class="contact" style="left:366px;top:1386px">
    <svg width="14" height="18" viewBox="0 0 14 18"><path d="M7 0 A7 7 0 0 1 14 7 C14 12 7 18 7 18 C7 18 0 12 0 7 A7 7 0 0 1 7 0 Z" fill="#7dc242"/><circle cx="7" cy="7" r="2.5" fill="#fff"/></svg>
    <span>Seacliff Bay, SA 5049 Seacliff<br>Bay, SA 5049</span>
  </div>
  <div class="contact" style="left:366px;top:1452px">
    <svg width="16" height="16" viewBox="0 0 16 16"><rect x="1" y="4" width="14" height="10" rx="1" fill="#13a88f"/><rect x="4" y="1" width="8" height="5" fill="#13a88f"/><rect x="4" y="7" width="8" height="2" fill="#fff"/></svg>
    <span>08 6000 5678</span>
  </div>

  <div class="web-bar">www.northgatewellness.com.au</div>
</main>
</body>
</html>
```